New, modern business card for growing audiology practice

We need a new business card for our audiology practice. Our logo and website have recently changed (more modern) and we want our business cards to reflect this change.
We conduct hearing tests, perform earwax removals, and fit & dispense hearing aids to our patients. We are a family owned practice in which the owner is the one who works directly with the patient. I have attached logos in various formats to use, as well as two ideas I found on this website; as well as a scanned copy of our current logo. Good luck!

Industry/Entity Type

Business

Contact Information for Business Card

Company name: Tolvera Hearing Center
Provider name: Peter Wolstenby, Au.D. F/NSB
Phone number: (440) 683-5127
Address: 837 W. Lindell Ave. Marlow Heights, OH 44391
email: tolverahearing@postvane.com
website: tolverahearing.com

Colors
000000
aaaaaa
dbdbdb
cacaca
9bcb3c
afd23c
cadf82
b1b1b1

Requirements
Must have
• My card must include information in the "details" section. In the attached images, I found a few that I liked and I would like to model after - "brisky bouncin'" and "Sound Method Center".
• Must be horizontal.
• Must include logos provided. I uploaded them in various file formats and various ways.
• Must match logo font, if possible, if not, please get as close as you can.
Nice to have
• I really like the idea of having a color on one side with just the logo and company name and the contact information and provider name on the other side. I also really like the idea of having the main color dominating on the logo/company side with accent of that same color on the contact side of the card.
Should not have
• Must not be vertical.

```html
<!DOCTYPE html>
<html lang="en">
<head>
<meta charset="utf-8">
<title>Tolvera Hearing Center — Business Card</title>
<link href="https://fonts.googleapis.com/css2?family=Montserrat:wght@400;500;600&display=swap" rel="stylesheet">
<style>
  :root {
    --stage: #d9d9d9;
    --card-dark: #262626;
    --card-light: #f7f7f7;
    --card-light-edge: #e6e6e6;
    --green: #8dc03b;
    --green-soft: #afd23c;
    --ink: #3a3a3a;
    --ink-soft: #555555;
    --white: #ffffff;
  }
  * { margin: 0; padding: 0; box-sizing: border-box; }
  html, body { width: 1200px; height: 834px; overflow: hidden; }
  body {
    background: var(--stage);
    font-family: "Montserrat", sans-serif;
    display: flex;
    flex-direction: column;
    align-items: center;
    justify-content: center;
    gap: 40px;
  }
  .card {
    width: 640px;
    height: 366px;
    position: relative;
    overflow: hidden;
    box-shadow: 0 6px 18px rgba(0,0,0,0.18);
  }

  /* Front side */
  .card-front { background: var(--card-dark); }
  .front-brand {
    position: absolute;
    top: 150px;
    left: 0; right: 0;
    display: flex;
    align-items: center;
    justify-content: center;
    gap: 14px;
  }
  .brand-dot {
    width: 26px; height: 26px;
    border-radius: 50%;
    background: var(--green);
    flex: none;
  }
  .front-name {
    color: var(--white);
    font-weight: 400;
    font-size: 30px;
    letter-spacing: -0.5px;
    text-transform: uppercase;
  }
  .web-tab {
    position: absolute;
    bottom: 0;
    left: 340px;
    width: 230px;
    height: 50px;
    background: var(--green);
    border-radius: 18px 18px 0 0;
    display: flex;
    align-items: center;
    justify-content: center;
    color: var(--white);
    font-size: 13px;
    letter-spacing: 0.2px;
  }

  /* Back side */
  .card-back {
    background: linear-gradient(120deg, var(--card-light) 0%, var(--white) 55%, var(--card-light-edge) 100%);
  }
  .back-brand {
    position: absolute;
    left: 70px;
    top: 128px;
    display: flex;
    align-items: center;
    gap: 18px;
  }
  .back-brand .brand-dot { width: 40px; height: 40px; }
  .back-name {
    color: var(--ink);
    font-weight: 500;
    font-size: 27px;
    line-height: 1.02;
    text-transform: uppercase;
    letter-spacing: -0.3px;
  }
  .details {
    position: absolute;
    left: 330px;
    top: 92px;
    color: var(--ink-soft);
  }
  .provider {
    color: var(--green);
    font-weight: 600;
    font-size: 15px;
    text-transform: uppercase;
    letter-spacing: 0.2px;
    margin-bottom: 16px;
  }
  .address {
    font-style: normal;
    font-size: 11.5px;
    line-height: 1.55;
    margin-left: 18px;
    margin-bottom: 18px;
  }
  .contact-list { list-style: none; }
  .contact-list li {
    display: flex;
    align-items: center;
    gap: 12px;
    font-size: 11.5px;
    line-height: 1;
    margin-bottom: 8px;
  }
  .contact-icon { width: 13px; height: 13px; flex: none; }
</style>
</head>
<body>

  <section class="card card-front" aria-label="Card front">
    <div class="front-brand">
      <span class="brand-dot"></span>
      <span class="front-name">Tolvera Hearing Center</span>
    </div>
    <div class="web-tab">www.tolverahearing.com</div>
  </section>

  <section class="card card-back" aria-label="Card back">
    <div class="back-brand">
      <span class="brand-dot"></span>
      <span class="back-name">Tolvera<br>Hearing<br>Center</span>
    </div>

    <div class="details">
      <p class="provider">Peter Wolstenby, Au.D. F/NSB</p>
      <address class="address">
        837 W. Lindell Ave.<br>
        Marlow Heights, OH 44391
      </address>
      <ul class="contact-list">
        <li>
          <svg class="contact-icon" viewBox="0 0 16 16" fill="none" stroke="var(--green)" stroke-width="1.6" stroke-linejoin="round">
            <path d="M2 6c0-2 2.5-3 6-3s6 1 6 3l-2.5 1L10 5.5H6L4.5 7z"/>
            <rect x="3.5" y="8" width="9" height="5" rx="1"/>
          </svg>
          <span>(440) 683-5127</span>
        </li>
        <li>
          <svg class="contact-icon" viewBox="0 0 16 16" fill="none" stroke="var(--green)" stroke-width="1.6" stroke-linejoin="round">
            <rect x="1.5" y="3.5" width="13" height="9"/>
            <path d="M1.5 3.5 8 9l6.5-5.5"/>
          </svg>
          <span>tolverahearing@postvane.com</span>
        </li>
        <li>
          <svg class="contact-icon" viewBox="0 0 16 16" fill="none" stroke="var(--green)" stroke-width="1.5">
            <circle cx="8" cy="8" r="6.3"/>
            <ellipse cx="8" cy="8" rx="2.8" ry="6.3"/>
            <path d="M1.7 8h12.6"/>
          </svg>
          <span>www.tolverahearing.com</span>
        </li>
      </ul>
    </div>
  </section>

</body>
</html>
```